The Aldermoor- outdoor banner

This should be a horizontal banner. It should have the logos attached incorporated and the following details
Coming Spring 2025: The Aldermoor - Exclusive Luxury Condos
Listed by Marisol Quennell | Fairlight Realty
Construction by Stonegate Build Group
Unveil the height of luxury living with The Aldermoor, a new condo building in East Boston, set for completion in Spring 2025. Experience a standard of elegance and sophistication like never before.
For more information and inquiries, please contact:
Marisol Quennell
Phone: (617) 430-9162
Email: marisol@fairlightprops.com
The banner should be very classy incorporting gold and navy very classic fonts. The Aldermoor should look very classy and exclusive. The stonegate build group logo should be smaller. It should not include their phone number and instagram handle only the name of the company. Herringbone pattern in the background would be great. This is going outside the building to advertise pre construction units

```html
<!DOCTYPE html>
<html lang="en">
<head>
<meta charset="utf-8">
<title>The Aldermoor – Outdoor Banner</title>
<link href="https://fonts.googleapis.com/css2?family=Cinzel:wght@400;600;700&family=Montserrat:wght@500&family=Poppins:wght@500;600&display=swap" rel="stylesheet">
<style>
  :root {
    --navy: #18254a;
    --navy-deep: #121d3d;
    --navy-panel: #1f2f57;
    --gold: #d9aa5b;
    --gold-light: #edc274;
    --gold-dark: #c6964a;
    --ink: #1b2240;
    --page: #ffffff;
  }
  * { margin: 0; padding: 0; box-sizing: border-box; }
  html, body { width: 981px; height: 1200px; overflow: hidden; background: var(--page); }
  .canvas { position: relative; width: 981px; height: 1200px; }

  .banner {
    position: absolute; left: 20px; top: 462px;
    width: 941px; height: 275px;
    background: linear-gradient(90deg, var(--navy) 0%, var(--navy-deep) 100%);
    box-shadow: 0 10px 22px rgba(0,0,0,.28);
    overflow: hidden;
  }
  .brand-panel {
    position: absolute; left: 10px; top: 9px; width: 226px; height: 147px;
    background: var(--navy-panel);
  }
  .frame {
    position: absolute; left: 10px; top: 9px; width: 919px; height: 147px;
    border: 1px solid var(--gold);
  }
  .realty-name {
    position: absolute; left: 10px; top: 94px; width: 226px; text-align: center;
    font-family: "Cinzel", serif; font-weight: 400; font-size: 24px;
    color: var(--gold); letter-spacing: .5px; line-height: 1;
  }
  .realty-sub {
    position: absolute; left: 10px; top: 124px; width: 226px; text-align: center;
    font-family: "Cinzel", serif; font-weight: 400; font-size: 9px;
    color: var(--gold); letter-spacing: 8px; line-height: 1; padding-left: 8px;
  }

  .headline { position: absolute; left: 246px; top: 26px; }
  .headline .eyebrow {
    font-family: "Montserrat", sans-serif; font-weight: 500; font-size: 24px;
    letter-spacing: 7.3px; color: var(--gold); line-height: 1;
  }
  .headline .title {
    margin-top: 4px;
    font-family: "Cinzel", serif; font-weight: 700; font-size: 55px;
    color: var(--gold); line-height: 1; letter-spacing: .5px;
  }
  .headline .subtitle {
    margin-top: 3px;
    font-family: "Cinzel", serif; font-weight: 400; font-size: 34px;
    color: var(--gold); line-height: 1;
  }

  .builder-name {
    position: absolute; left: 810px; top: 66px; width: 112px; text-align: center;
    font-family: "Cinzel", serif; font-weight: 600; font-size: 11px;
    color: var(--gold); line-height: 1.25; letter-spacing: .4px;
  }

  .gold-band {
    position: absolute; left: 0; top: 166px; width: 420px; height: 109px;
    background: linear-gradient(90deg, var(--gold-dark), var(--gold-light) 70%, var(--gold));
  }
  .construction { position: absolute; left: 38px; top: 174px; width: 340px; }
  .construction h2 {
    font-family: "Cinzel", serif; font-weight: 600; font-size: 14.5px;
    color: var(--ink); line-height: 1.2; letter-spacing: .2px;
  }
  .construction p {
    margin-top: 3px;
    font-family: "Poppins", sans-serif; font-weight: 600; font-size: 10.2px;
    color: var(--ink); line-height: 1.38;
  }

  .agent-arch {
    position: absolute; left: 393px; top: 150px; width: 103px; height: 125px;
    background: var(--navy); border-radius: 52px 52px 0 0;
  }
  .agent-photo {
    position: absolute; left: 403px; top: 160px; width: 83px; height: 115px;
    border-radius: 42px 42px 0 0;
    background: linear-gradient(180deg, #cfcfcf 0%, #8a8a8a 55%, #4a4a4a 100%);
  }

  .listing { position: absolute; left: 507px; top: 175px; }
  .listing .label, .listing .firm {
    font-family: "Cinzel", serif; font-weight: 400; font-size: 12.5px;
    color: var(--gold); line-height: 1;
  }
  .listing .agent {
    margin: 2px 0 3px;
    font-family: "Cinzel", serif; font-weight: 700; font-size: 17.5px;
    color: var(--gold); line-height: 1;
  }

  .contact { position: absolute; left: 713px; top: 180px; }
  .contact .row { display: flex; align-items: center; gap: 7px; color: var(--gold); }
  .contact .phone { font-family: "Cinzel", serif; font-weight: 400; font-size: 20px; line-height: 1; }
  .contact .email { font-family: "Poppins", sans-serif; font-weight: 500; font-size: 10.5px; line-height: 1; margin-top: 6px; }
  .contact svg { flex: none; }

  .web-band {
    position: absolute; left: 496px; top: 233px; width: 445px; height: 42px;
    background: linear-gradient(90deg, var(--gold), var(--gold-light));
    display: flex; align-items: center; justify-content: center;
    font-family: "Poppins", sans-serif; font-weight: 600; font-size: 19px;
    letter-spacing: 4.4px; color: var(--ink);
  }
</style>
</head>
<body>
<div class="canvas">
  <section class="banner">
    <div class="brand-panel"></div>
    <div class="frame"></div>

    <div class="realty-name">FAIRLIGHT</div>
    <div class="realty-sub">REALTY</div>

    <div class="headline">
      <div class="eyebrow">COMING SPRING 2025</div>
      <h1 class="title">THE ALDERMOOR</h1>
      <div class="subtitle">EXCLUSIVE LUXURY CONDOS</div>
    </div>

    <div class="builder-name">STONEGATE BUILD GROUP</div>

    <div class="gold-band"></div>
    <div class="construction">
      <h2>CONSTRUCTION BY STONEGATE BUILD GROUP</h2>
      <p>Unveil the height of luxury living with The Aldermoor, a new condo building in East Boston, set for completion in Spring 2025. Experience a standard of elegance and sophistication like never before.</p>
    </div>

    <div class="agent-arch"></div>
    <div class="agent-photo" role="img" aria-label="Black and white portrait of listing agent Marisol Quennell seated on a chair"></div>

    <div class="listing">
      <div class="label">LISTED BY</div>
      <div class="agent">MARISOL QUENNELL</div>
      <div class="firm">FAIRLIGHT REALTY</div>
    </div>

    <div class="contact">
      <div class="row phone">
        <svg width="16" height="16" viewBox="0 0 16 16" aria-hidden="true">
          <circle cx="8" cy="8" r="8" fill="#d9aa5b"/>
          <path d="M5 4.2c.4-.3.9-.2 1.1.2l.7 1.3c.2.4.1.8-.2 1l-.5.4c.4.9 1.1 1.6 2 2l.4-.5c.3-.3.7-.4 1-.2l1.3.7c.4.2.5.7.2 1.1l-.6.7c-.4.4-1 .5-1.6.3C6.9 10.4 5.6 9.1 4.8 7.2c-.2-.6-.1-1.2.3-1.6z" fill="#18254a"/>
        </svg>
        <span>(617) 430-9162</span>
      </div>
      <div class="row email">
        <svg width="16" height="16" viewBox="0 0 16 16" aria-hidden="true">
          <circle cx="8" cy="8" r="8" fill="#d9aa5b"/>
          <rect x="4.3" y="5.3" width="7.4" height="5.2" rx=".6" fill="#18254a"/>
          <path d="M4.6 5.7 8 8.2l3.4-2.5" stroke="#d9aa5b" stroke-width=".8" fill="none"/>
        </svg>
        <span>marisol@fairlightprops.com</span>
      </div>
    </div>

    <div class="web-band">fairlightprops.com</div>
  </section>
</div>
</body>
</html>
```